Super elegant, crisp & clean Business card design required

We recently upgraded our branding - which is on our website - talvendoraphoto.com

I would like a simple, yet elegant, clean business card design please.

The font of my logo is Cinzel - and because of the natural colour - it's best to have this on a black background.

I would like to have the back of the business card - with simply my logo.

PLEASE DO NOT SUBMIT A COMPLICATED / UNCLEAN DESIGN

Industry/Entity Type

Business

Contact Information for Business Card

Talven Doroshko Photography

Font styles to use
Other font styles liked:
• Cinzel

Requirements
Must have
• A backpage with nothing but my logo
• Simple design - stands out
Should not have
• Colour that dont align with my logo
• Over complicated '/ non symmetrical design

```html
<!DOCTYPE html>
<html lang="en">
<head>
<meta charset="utf-8">
<title>Talven Doroshko Photography – Business Card</title>
<link rel="stylesheet" href="https://fonts.googleapis.com/css2?family=Cinzel:wght@400;700&display=swap">
<style>
  :root {
    --stage: #2b2b2b;
    --card: #050505;
    --ink: #ffffff;
    --ink-soft: #d9d9d9;
  }
  * { margin: 0; padding: 0; box-sizing: border-box; }
  html, body { width: 1200px; height: 900px; overflow: hidden; }
  body {
    background: var(--stage);
    font-family: "Cinzel", serif;
    color: var(--ink);
    position: relative;
  }
  .card {
    position: absolute;
    width: 600px;
    height: 343px;
    background: var(--card);
    border-radius: 22px;
    overflow: hidden;
    box-shadow: 0 18px 40px rgba(0,0,0,0.55);
  }
  .card--back { left: 150px; top: 70px; }
  .card--front { left: 450px; top: 487px; }

  /* back: name mark only */
  .back-mark {
    position: absolute;
    inset: 0;
    display: flex;
    align-items: center;
    justify-content: center;
    gap: 16px;
  }
  .mark-dot {
    width: 12px; height: 12px;
    border: 1px solid var(--ink);
    border-radius: 50%;
  }
  .back-mark .mark-name {
    font-size: 30px;
    font-weight: 400;
    letter-spacing: 3px;
  }

  /* front */
  .brand {
    position: absolute;
    left: 46px; top: 78px;
    width: 250px;
    text-align: center;
    font-weight: 400;
  }
  .brand .mark-name { font-size: 21px; letter-spacing: 1px; line-height: 1.2; }
  .brand .mark-sub { font-size: 11px; letter-spacing: 7px; color: var(--ink-soft); margin-top: 4px; }

  .signature {
    position: absolute;
    right: 34px; top: 110px;
    width: 250px;
    text-align: right;
  }
  .signature .person { font-size: 19px; font-weight: 700; letter-spacing: 0.5px; }
  .signature .role { font-size: 12px; color: var(--ink-soft); margin-top: 2px; padding-bottom: 5px; border-bottom: 1.5px solid var(--ink); }

  .stripe { position: absolute; inset: 0; }

  .contacts {
    position: absolute;
    left: 36px; bottom: 26px;
    list-style: none;
    font-size: 13px;
    letter-spacing: 0.5px;
  }
  .contacts li { display: flex; align-items: center; gap: 10px; height: 21px; }
  .contacts svg { width: 12px; height: 12px; fill: var(--ink); }
</style>
</head>
<body>
  <section class="card card--back" aria-label="Card back">
    <div class="back-mark">
      <span class="mark-dot"></span>
      <span class="mark-name">Talven Doroshko</span>
    </div>
  </section>

  <section class="card card--front" aria-label="Card front">
    <div class="brand">
      <div class="mark-name">Talven Doroshko</div>
      <div class="mark-sub">Photography</div>
    </div>

    <div class="signature">
      <div class="person">Talven Doroshko</div>
      <div class="role">Photography</div>
    </div>

    <svg class="stripe" viewBox="0 0 600 343" aria-hidden="true">
      <line x1="0" y1="240" x2="398" y2="240" stroke="#fff" stroke-width="2"/>
      <polygon points="408,228 600,228 600,343 396,343" fill="#fff"/>
      <rect x="0" y="332" width="600" height="11" fill="#fff"/>
    </svg>

    <ul class="contacts">
      <li>
        <svg viewBox="0 0 24 24"><path d="M6.6 10.8a15.1 15.1 0 0 0 6.6 6.6l2.2-2.2c.3-.3.7-.4 1-.2 1.1.4 2.3.6 3.6.6.6 0 1 .4 1 1V20c0 .6-.4 1-1 1A17 17 0 0 1 3 4c0-.6.4-1 1-1h3.5c.6 0 1 .4 1 1 0 1.3.2 2.5.6 3.6.1.3 0 .7-.2 1z"/></svg>
        <span>+330 2471-5930</span>
      </li>
      <li>
        <svg viewBox="0 0 24 24"><path d="M2 5h20v14H2zm2 2v.5l8 5 8-5V7zm0 2.8V17h16V9.8l-8 5z"/></svg>
        <span>INFO@TALVENDORAPHOTO.COM</span>
      </li>
      <li>
        <svg viewBox="0 0 24 24"><path d="M12 2a10 10 0 1 0 0 20 10 10 0 0 0 0-20zm6.9 6h-3a15 15 0 0 0-1.3-3.9A8 8 0 0 1 18.9 8zM12 4c.8 1.2 1.5 2.5 1.9 4h-3.8c.4-1.5 1.1-2.8 1.9-4zM4.3 14a8 8 0 0 1 0-4h3.4a16 16 0 0 0 0 4zm.8 2h3a15 15 0 0 0 1.3 3.9A8 8 0 0 1 5.1 16zm3-8h-3a8 8 0 0 1 4.3-3.9A15 15 0 0 0 8.1 8zM12 20c-.8-1.2-1.5-2.5-1.9-4h3.8c-.4 1.5-1.1 2.8-1.9 4zm2.3-6H9.7a14 14 0 0 1 0-4h4.6a14 14 0 0 1 0 4zm.3 5.9a15 15 0 0 0 1.3-3.9h3a8 8 0 0 1-4.3 3.9zm1.7-5.9a16 16 0 0 0 0-4h3.4a8 8 0 0 1 0 4z"/></svg>
        <span>WWW.TALVENDORAPHOTO.COM</span>
      </li>
    </ul>
  </section>
</body>
</html>
```